New business card for a regional office of a US M&A company

We need business card for a finance company, office based in Hong Kong , our Head office is in US, our business is to Merge and acquires companies , the new office will be a regional office for the Asia Pacific region. We want to use the head office logo as attached ( but don't have to be exactly the same, can be a variation to it) as a base and then add Asia Pacific alongside the logo.
We would prefer to have be bilingual Eng + Chinese, although we don't really have Chinese company name .

Industry/Entity Type

Business

Contact Information for Business Card

Clara Jo Tsang
 

VP,
APAC M&A Operations
Orin Vantage Asia Pacific Limited
 
Unit 1407, K18
18 Tai Lok Shan Road, 
Hong Kong 
 
M: +852 6038 1742
T : +852 2836 4100
F : +852 2836 4177
VOIP: 4158
 
cjtsang@orinvantage.com

Font styles to use
Serif
Sans Serif

Colors

Designer to choose colors to be used in the design.

Requirements
Must have
• APAC Office

```html
<!DOCTYPE html>
<html lang="en">
<head>
<meta charset="utf-8">
<title>Orin Vantage – Business Card</title>
<link rel="stylesheet" href="https://fonts.googleapis.com/css2?family=Open+Sans:wght@700&family=Roboto:wght@400&family=Roboto+Condensed:wght@500&display=swap">
<style>
  :root {
    --backdrop: #7a5238;
    --card-navy: #0f2842;
    --brand-cyan: #1fa8d0;
    --text-white: #e9eef3;
    --rule-grey: #8e9cab;
  }
  * { margin: 0; padding: 0; box-sizing: border-box; }
  html, body {
    width: 1200px; height: 960px; overflow: hidden;
    background: var(--backdrop);
  }
  .stage { position: relative; width: 1200px; height: 960px; }
  .card {
    position: absolute; width: 600px; height: 343px;
    background: var(--card-navy);
    box-shadow: 0 2px 6px rgba(0,0,0,0.35);
    color: var(--text-white);
    font-family: "Roboto", Arial, sans-serif;
  }
  .card--front { left: 314px; top: 113px; }
  .card--back  { left: 311px; top: 472px; }

  .brand {
    position: absolute;
    display: flex; align-items: center; gap: 12px;
    font-family: "Open Sans", Arial, sans-serif;
    font-weight: 700; color: var(--brand-cyan);
    white-space: nowrap; line-height: 1;
  }
  .brand__mark { display: block; background: var(--brand-cyan); }
  .card--front .brand { right: 31px; top: 120px; font-size: 38px; }
  .card--front .brand__mark { width: 14px; height: 14px; }
  .card--back .brand { left: 0; right: 0; justify-content: center; top: 190px; font-size: 48px; }
  .card--back .brand__mark { width: 18px; height: 18px; }

  .holder__name {
    position: absolute; left: 29px; top: 176px;
    font-family: "Roboto Condensed", Arial, sans-serif;
    font-weight: 500; font-size: 21px; color: var(--brand-cyan);
    text-transform: uppercase; letter-spacing: 0.2px;
  }
  .holder__title { position: absolute; left: 30px; top: 203px; font-size: 14px; }
  .holder__rule {
    position: absolute; left: 58px; right: 32px; top: 209px;
    height: 1px; background: var(--rule-grey);
  }

  .contact-list { position: absolute; left: 31px; top: 230px; list-style: none; font-size: 14px; }
  .contact-list li { display: flex; align-items: center; gap: 8px; height: 19px; }
  .contact-list svg { width: 13px; height: 13px; fill: var(--brand-cyan); }
  .contact-list .voip { margin-top: 8px; gap: 0; }

  .office-address {
    position: absolute; right: 33px; top: 223px;
    text-align: right; font-size: 14px; line-height: 18.7px; font-style: normal;
  }

  .web-address {
    position: absolute; left: 0; right: 0; top: 284px;
    text-align: center; font-size: 14px; letter-spacing: 8.2px;
  }
</style>
</head>
<body>
<main class="stage">

  <section class="card card--front" aria-label="Card front">
    <div class="brand"><span class="brand__mark"></span>ORIN VANTAGE</div>

    <h1 class="holder__name">Clara Jo Tsang</h1>
    <p class="holder__title">VP</p>
    <div class="holder__rule"></div>

    <ul class="contact-list">
      <li>
        <svg viewBox="0 0 24 24" aria-label="Telephone"><path d="M6.6 10.8a15.1 15.1 0 0 0 6.6 6.6l2.2-2.2a1 1 0 0 1 1-.25 11.4 11.4 0 0 0 3.6.57 1 1 0 0 1 1 1V20a1 1 0 0 1-1 1A17 17 0 0 1 3 4a1 1 0 0 1 1-1h3.5a1 1 0 0 1 1 1c0 1.25.2 2.45.57 3.6a1 1 0 0 1-.25 1z"/></svg>
        +852 2836 4100
      </li>
      <li>
        <svg viewBox="0 0 24 24" aria-label="Mobile"><path d="M7 1h10a2 2 0 0 1 2 2v18a2 2 0 0 1-2 2H7a2 2 0 0 1-2-2V3a2 2 0 0 1 2-2zm0 3v14h10V4z"/></svg>
        +852 6038 1742
      </li>
      <li>
        <svg viewBox="0 0 24 24" aria-label="Fax"><path d="M6 2h9l3 3v5H6zM3 11h18a1 1 0 0 1 1 1v8a1 1 0 0 1-1 1H3a1 1 0 0 1-1-1v-8a1 1 0 0 1 1-1zm3 3v2h12v-2z"/></svg>
        +852 2836 4177
      </li>
      <li class="voip">VOIP: 4158</li>
    </ul>

    <address class="office-address">
      APAC M&amp;A Operations<br>
      Orin Vantage Asia Pacific Limited<br>
      Unit 1407, K18<br>
      18 Tai Lok Shan Road<br>
      Hong Kong
    </address>
  </section>

  <section class="card card--back" aria-label="Card back">
    <div class="brand"><span class="brand__mark"></span>ORIN VANTAGE</div>
    <p class="web-address">www.orinvantage.com</p>
  </section>

</main>
</body>
</html>
```